Recruiting Firm Need Professional, Modern Tri-Fold Brochure for their United States Based Business

-We need a professional, modern TRI-FOLD brochure design that can help generate business for our recruiting firm. We need an impressive brochure.
- Please use the about us website content and attached website content. Website: www.morvellstaffingpartners.example
- Please use logo files attached.
- Please note: This brochure will be the starting point for an upgraded website design so we are NOT looking for a brochure to look like our current website.
- We want potential clients to want to do business with us just based on the brochure look and feel alone.

Target Market(s)

small, medium, and large companies who need administrative, human resources, and accounting talent

Industry/Entity Type

Professional Service

Font styles to use
Serif

Requirements
Must have
• - Professional, Modern TRI-FOLD Brochure Design for United States Based Company
• - Please show diverse group of professionals pictures similar to the ones on our website. One pic must include an African American female and one pic must include an African male. Or both an African American female and male can be include in the group of other races. But All the group photos must be diverse in race and include both male and female.
• - Please show pics of one business professional too
• a diverse group photo would be nice on the front cover...so we can show diversity and inclusion from the start
Should not have
• - Please DO NOT use the same pictures on our website.

```html
<!DOCTYPE html>
<html lang="en">
<head>
<meta charset="utf-8">
<title>Morvell Staffing Partners – Tri-Fold Brochure</title>
<link rel="stylesheet" href="https://fonts.googleapis.com/css2?family=Open+Sans:wght@400;600;700&display=swap">
<style>
  :root{
    --red:#b30f12;
    --red-deep:#7e0a0c;
    --red-text:#a8141a;
    --ink:#1e1e1e;
    --black:#111111;
    --paper:#ffffff;
    --panel:#f6f6f6;
    --stage:#e4e4e4;
  }
  *{box-sizing:border-box;margin:0;padding:0}
  html,body{width:1200px;height:887px;overflow:hidden}
  body{background:var(--stage);font-family:"Open Sans",Arial,sans-serif;color:var(--ink);position:relative}
  .brochure{position:absolute;left:30px;top:41px;width:1140px;height:805px;background:var(--paper);overflow:hidden;box-shadow:0 4px 14px rgba(0,0,0,.25)}
  .panel-bg{position:absolute;top:0;height:805px}
  .panel-bg.left{left:0;width:380px;background:linear-gradient(#ffffff,var(--panel))}
  .panel-bg.wide{left:380px;width:760px;background:linear-gradient(135deg,#f3f3f3,#ffffff 45%,#ececec)}
  .photo{position:absolute}
  .photo.professional{left:12px;top:440px;width:368px;height:200px;background:linear-gradient(#ececec,#cfcfcf 60%,#3a3a3a)}
  .photo.meeting{left:482px;top:318px;width:658px;height:420px;background:radial-gradient(ellipse at 55% 50%,#dfe6e6,#eeeeee 55%,#f4f4f4)}
  .fold{position:absolute;top:0;width:1px;height:805px;background:rgba(0,0,0,.07);z-index:3}
  .fold.one{left:380px}.fold.two{left:761px}
  .tab{position:absolute;top:23px;height:34px;background:var(--red);color:#fff;font-size:18px;font-weight:600;line-height:34px;padding-left:36px}
  .tab::after{content:"";position:absolute;top:0;right:-30px;width:22px;height:34px;background:var(--black);transform:skewX(38deg)}
  .tab.who{left:0;width:214px}
  .tab.difference{left:380px;width:342px;padding-left:34px}
  .subhead{position:absolute;color:var(--red-text);font-weight:600;font-size:15.5px;line-height:20px}
  .subhead.who{left:35px;top:72px}
  .subhead.difference{left:415px;top:72px}
  .about{position:absolute;left:35px;top:124px;width:305px;font-size:11.6px;line-height:16.6px;text-align:justify}
  .points{position:absolute;left:415px;top:124px;width:330px;list-style:none}
  .points li{position:relative;padding-left:23px;font-size:11.8px;line-height:16.6px;margin-bottom:12px}
  .points svg{position:absolute;left:0;top:2px;width:14px;height:13px}
  .headline{position:absolute;left:809px;top:30px;font-size:36px;line-height:46px;font-weight:400;color:var(--red-text)}
  .waves{position:absolute;left:0;top:0;width:1140px;height:805px;z-index:2}
  .contact{position:absolute;top:736px;width:380px;text-align:center;color:#fff;z-index:4}
  .contact.left{left:0}.contact.right{left:761px}
  .phone{font-size:20px;line-height:24px;display:flex;align-items:center;justify-content:center;gap:9px}
  .web{font-size:14px;line-height:20px;margin-top:8px;display:flex;align-items:center;justify-content:center;gap:7px}
  .phone svg{width:18px;height:18px}.web svg{width:12px;height:12px}
</style>
</head>
<body>
<main class="brochure">
  <div class="panel-bg left"></div>
  <div class="panel-bg wide"></div>

  <div class="photo professional" role="img" aria-label="Photo of a smiling business professional seated at a desk with a computer monitor"></div>
  <div class="photo meeting" role="img" aria-label="Photo of a diverse team of professionals meeting around a glass conference table"></div>

  <svg class="waves" viewBox="0 0 1140 805" aria-hidden="true">
    <path d="M0,498 C260,620 640,760 1140,618 L1140,805 L0,805Z" fill="#111"/>
    <path d="M0,516 C270,640 650,772 1140,628 L1140,805 L0,805Z" fill="#7e0a0c"/>
    <path d="M0,560 C280,690 660,790 1140,636 L1140,805 L0,805Z" fill="#b30f12"/>
    <path d="M0,598 C300,735 700,800 1140,642 L1140,662 C700,815 300,760 0,630Z" fill="#fff"/>
    <path d="M0,630 C300,760 700,815 1140,662 L1140,805 L0,805Z" fill="#b30f12"/>
  </svg>

  <div class="fold one"></div>
  <div class="fold two"></div>

  <section class="panel who-we-are">
    <h2 class="tab who">Who We Are</h2>
    <h3 class="subhead who">A Top-Notch Resource for Administrative,<br>Human Resources, and Accounting Talent</h3>
    <p class="about">Morvell Staffing Partners is a professional search firm that specializes in providing top-notch administrative, human resources, and accounting talent. We provide best-in-class talent to companies seeking to simplify their recruiting process, increase efficiency, and optimize productivity. Each search is customized based on our client's unique requirements. We provide quality, timely, and efficient services. Our recruiters are highly skilled in identifying, screening, interviewing, and assessing candidates across various industries. We develop a partnership with our client and candidate in order to make the recruitment process a success for both parties.</p>
  </section>

  <section class="panel difference">
    <h2 class="tab difference">Experience the Morvell Difference</h2>
    <h3 class="subhead difference">We use our proprietary M-Strategy<br>approach to deliver high-quality results.</h3>
    <ul class="points">
      <li><svg viewBox="0 0 14 13"><path d="M1,7 L5,11 L13,1" fill="none" stroke="#b30f12" stroke-width="2.4"/></svg>Top-Notch Talent. We will only present candidates who meet 90% of your job requirements.</li>
      <li><svg viewBox="0 0 14 13"><path d="M1,7 L5,11 L13,1" fill="none" stroke="#b30f12" stroke-width="2.4"/></svg>Thorough. We listen to your needs and develop a recruiting checklist to make sure we cover all basis.</li>
      <li><svg viewBox="0 0 14 13"><path d="M1,7 L5,11 L13,1" fill="none" stroke="#b30f12" stroke-width="2.4"/></svg>Tenacious. We are passionate and persistent about meeting your expectations.</li>
      <li><svg viewBox="0 0 14 13"><path d="M1,7 L5,11 L13,1" fill="none" stroke="#b30f12" stroke-width="2.4"/></svg>Timely. We deliver quality results on time.</li>
    </ul>
  </section>

  <section class="panel cover">
    <h1 class="headline">We can find<br>the right talent for<br>your hiring needs.</h1>
  </section>

  <footer class="contact left">
    <p class="phone"><svg viewBox="0 0 18 18"><circle cx="9" cy="9" r="8" fill="none" stroke="#fff" stroke-width="1.4"/><path d="M6.2,4.6 L7.6,6.6 L6.8,7.6 C7.4,9 8.8,10.4 10.3,11.1 L11.3,10.3 L13.3,11.7 L12.3,13.2 C8.6,12.9 5.1,9.5 4.8,5.7Z" fill="#fff"/></svg>555-214-0387</p>
    <p class="web"><svg viewBox="0 0 12 12"><g fill="none" stroke="#fff" stroke-width="1"><circle cx="6" cy="6" r="5"/><ellipse cx="6" cy="6" rx="2.2" ry="5"/><path d="M1,6H11"/></g></svg>www.morvellstaffingpartners.example</p>
  </footer>
  <footer class="contact right">
    <p class="phone"><svg viewBox="0 0 18 18"><circle cx="9" cy="9" r="8" fill="none" stroke="#fff" stroke-width="1.4"/><path d="M6.2,4.6 L7.6,6.6 L6.8,7.6 C7.4,9 8.8,10.4 10.3,11.1 L11.3,10.3 L13.3,11.7 L12.3,13.2 C8.6,12.9 5.1,9.5 4.8,5.7Z" fill="#fff"/></svg>555-214-0387</p>
    <p class="web"><svg viewBox="0 0 12 12"><g fill="none" stroke="#fff" stroke-width="1"><circle cx="6" cy="6" r="5"/><ellipse cx="6" cy="6" rx="2.2" ry="5"/><path d="M1,6H11"/></g></svg>www.morvellstaffingpartners.example</p>
  </footer>
</main>
</body>
</html>
```